Consulting company requires a logo and business card design

I require a logo/business card design for a new company based in Sexsmith Alberta called TallMarsh Integrity Consulting Ltd. I plan to provide the following services: Construction management/inspection for the oil and gas industry, as well as general consulting for Asset Management, fleet management, etc. Have attached a copy of resume for use as guide for

Target Market(s)

Businesses within the oil and gas production, construction and shipping industry

Industry/Entity Type

Oil And Gas

Contact Information for Business Card

Believe should highlight, services offered, safety, quality,

Logo Text

TallMarsh Integrity Consulting (TMIC) ?

Font styles to use
Script

Requirements
Must have
• Open to all options

```html
<!DOCTYPE html>
<html lang="en">
<head>
<meta charset="utf-8">
<title>TallMarsh Integrity Consulting – Business Card</title>
<link rel="stylesheet" href="https://fonts.googleapis.com/css2?family=Questrial&family=Open+Sans:wght@400;600&display=swap">
<style>
  :root {
    --backdrop: #1c1c1c;
    --card-white: #ffffff;
    --band-top: #5b86c9;
    --band-bottom: #7fd0e4;
    --brand-blue: #3f8fd8;
    --name-blue: #5a9ad8;
    --ink: #333333;
    --ink-soft: #3a3a3a;
    --back-top: #5a82c6;
    --back-bottom: #7fd2e5;
    --mark-circle: #4f8fd6;
  }
  * { margin: 0; padding: 0; box-sizing: border-box; }
  html, body {
    width: 1200px; height: 900px; overflow: hidden;
    background: var(--backdrop);
  }
  .stage { position: relative; width: 1200px; height: 900px; }

  .card {
    position: absolute; top: 170px; width: 347px; height: 561px;
    box-shadow: 0 4px 14px rgba(0,0,0,0.55);
  }
  .card--front { left: 259px; background: var(--card-white); }
  .card--back {
    left: 631px;
    background: linear-gradient(to bottom, var(--back-top) 0%, var(--back-top) 20%, var(--back-bottom) 90%);
  }

  .band {
    position: absolute; left: 102px; width: 143px; height: 30px;
    background: linear-gradient(to bottom, var(--band-top), var(--band-bottom));
  }
  .band--top { top: 0; }
  .band--bottom { bottom: 0; height: 28px; }

  .brand-dot {
    position: absolute; left: 151px; top: 86px; width: 44px; height: 44px;
    border-radius: 50%; background: var(--brand-blue);
  }
  .brand-name {
    position: absolute; left: 0; right: 0; top: 164px; text-align: center;
    font-family: "Questrial", sans-serif; font-size: 44px; line-height: 1;
    color: var(--brand-blue); letter-spacing: 0.5px;
  }
  .brand-tagline {
    position: absolute; left: 0; right: 0; top: 223px; text-align: center;
    font-family: "Open Sans", sans-serif; font-size: 15px; letter-spacing: 3.2px;
    color: var(--ink);
  }

  .person-name {
    position: absolute; left: 0; right: 0; top: 278px; text-align: center;
    font-family: "Open Sans", sans-serif; font-size: 23px; letter-spacing: -0.3px;
    color: var(--name-blue);
  }
  .person-role {
    position: absolute; left: 0; right: 0; top: 310px; text-align: center;
    font-family: "Open Sans", sans-serif; font-size: 14px; color: var(--ink-soft);
  }

  .contact { position: absolute; left: 0; right: 0; text-align: center;
    font-family: "Open Sans", sans-serif; font-size: 14px; color: var(--ink-soft); }
  .contact--phone { top: 349px; }
  .contact--email { top: 370px; }
  .contact svg { vertical-align: -1px; margin-right: 8px; }

  .address {
    position: absolute; left: 0; right: 0; top: 465px; text-align: center;
    font-family: "Open Sans", sans-serif; font-size: 14px; line-height: 17px; color: var(--ink-soft);
  }

  .back-mark {
    position: absolute; left: 0; right: 0; top: 230px; text-align: center;
  }
  .back-mark__dot {
    display: block; margin: 0 auto 22px; width: 64px; height: 64px; border-radius: 50%;
    background: var(--mark-circle);
  }
  .back-mark__name {
    font-family: "Questrial", sans-serif; font-size: 40px; color: var(--card-white);
  }
</style>
</head>
<body>
<main class="stage">
  <section class="card card--front" aria-label="Business card front">
    <div class="band band--top"></div>
    <span class="brand-dot"></span>
    <h1 class="brand-name">TallMarsh</h1>
    <p class="brand-tagline">Integrity Consulting Ltd</p>

    <h2 class="person-name">DANA WHITLOCK</h2>
    <p class="person-role">Managing Director</p>

    <p class="contact contact--phone">
      <svg width="11" height="9" viewBox="0 0 11 9" aria-hidden="true"><path d="M1 3 Q5.5 0 10 3 L9 4.5 L7.5 4 L7.5 3 Q5.5 2.2 3.5 3 L3.5 4 L2 4.5 Z M2.5 5 L8.5 5 L9.5 8.5 L1.5 8.5 Z" fill="#5a9ad8"/></svg>555-014-2278
    </p>
    <p class="contact contact--email">
      <svg width="10" height="7" viewBox="0 0 10 7" aria-hidden="true"><rect x="0" y="0" width="10" height="7" fill="#5a9ad8"/><path d="M0 0 L5 4 L10 0" stroke="#fff" stroke-width="0.8" fill="none"/></svg>info@tallmarsh-mail.com
    </p>

    <p class="address">88 Ridgeline Road<br>Northfield, 482910</p>
    <div class="band band--bottom"></div>
  </section>

  <section class="card card--back" aria-label="Business card back">
    <div class="back-mark">
      <span class="back-mark__dot"></span>
      <p class="back-mark__name">TallMarsh</p>
    </div>
  </section>
</main>
</body>
</html>
```